Modern Business Card

Modern professional business card with more than just logo and demographic info. Something memorable.

We are a trendy/modern chiropractic group with an emphasis on neurology, hence the minimalist-type brain logo. We want to convey that modern and technical aspect with professionalism and the elite nature of our practice environment.

```html
<!DOCTYPE html>
<html lang="en">
<head>
<meta charset="utf-8">
<title>Meridian Spine — Business Card</title>
<link rel="stylesheet" href="https://fonts.googleapis.com/css2?family=EB+Garamond:wght@500&family=Montserrat:wght@400&display=swap">
<style>
  :root {
    --backdrop: #e4e4e4;
    --card-white: #ffffff;
    --card-dark: #1f1f1f;
    --brand-blue: #4a7fc4;
    --ink: #1e1e1e;
    --ink-soft: #4a4a4a;
    --ghost: #f1f1f1;
    --on-dark: #ffffff;
  }
  * { margin: 0; padding: 0; box-sizing: border-box; }
  html, body {
    width: 1200px; height: 1028px; overflow: hidden;
    background: var(--backdrop);
  }
  .card {
    position: absolute; left: 310px; width: 579px; height: 331px;
    box-shadow: 0 2px 6px rgba(0,0,0,0.18);
    overflow: hidden;
  }
  .card--front { top: 165px; background: var(--card-white); }
  .card--back { top: 532px; background: var(--card-dark); }

  .ghost-mark {
    position: absolute; left: 322px; top: 40px;
    width: 230px; height: 230px; border-radius: 50%;
    background: var(--ghost);
  }

  .brand { position: absolute; display: flex; align-items: center; }
  .brand__square { background: var(--brand-blue); flex: none; }
  .brand__name {
    font-family: "EB Garamond", Georgia, serif; font-weight: 500;
    letter-spacing: 0.02em; white-space: nowrap; line-height: 1;
  }
  .card--front .brand { left: 28px; top: 42px; gap: 12px; }
  .card--front .brand__square { width: 34px; height: 34px; }
  .card--front .brand__name { font-size: 27px; color: var(--ink); }

  .card--back .brand { left: 0; right: 0; top: 140px; justify-content: center; gap: 18px; }
  .card--back .brand__square { width: 50px; height: 50px; }
  .card--back .brand__name { font-size: 40px; color: var(--on-dark); }

  .person { position: absolute; left: 28px; top: 178px; }
  .person__name {
    font-family: "EB Garamond", Georgia, serif; font-weight: 500;
    font-size: 22px; color: var(--brand-blue); letter-spacing: 0.01em; line-height: 1;
  }
  .person__role {
    font-family: "Montserrat", Arial, sans-serif; font-size: 13.5px;
    color: var(--ink-soft); margin-top: 7px; letter-spacing: 0.03em;
  }
  .divider {
    position: absolute; left: 28px; width: 522px; top: 229px;
    height: 2px; background: var(--brand-blue);
  }
  .contact, .address {
    position: absolute; font-family: "Montserrat", Arial, sans-serif;
    font-size: 13.5px; color: var(--ink-soft); letter-spacing: 0.03em; line-height: 20px;
    list-style: none;
  }
  .contact { left: 28px; top: 244px; }
  .contact li { display: flex; align-items: center; gap: 9px; }
  .contact svg { width: 12px; height: 12px; flex: none; }
  .contact .accent { color: var(--brand-blue); }
  .address { right: 29px; top: 264px; text-align: right; font-style: normal; }
</style>
</head>
<body>
  <section class="card card--front" aria-label="Business card front">
    <div class="ghost-mark" aria-hidden="true"></div>
    <div class="brand">
      <span class="brand__square" aria-hidden="true"></span>
      <span class="brand__name">MERIDIAN SPINE</span>
    </div>
    <div class="person">
      <p class="person__name">DANIEL HAYES</p>
      <p class="person__role">Director</p>
    </div>
    <div class="divider"></div>
    <ul class="contact">
      <li>
        <svg viewBox="0 0 12 12" aria-hidden="true"><path d="M3 1 L5 3.5 L4 4.8 Q5 7.5 7.2 8 L8.5 7 L11 9 L9.8 11 Q3 10.5 1 2.2 Z" fill="none" stroke="#4a7fc4" stroke-width="1.1" stroke-linejoin="round"/></svg>
        (541) 555-0148
      </li>
      <li>
        <svg viewBox="0 0 12 12" aria-hidden="true"><rect x="1" y="2.5" width="10" height="7" fill="none" stroke="#4a7fc4" stroke-width="1.1"/><path d="M1 2.5 L6 6.5 L11 2.5" fill="none" stroke="#4a7fc4" stroke-width="1.1"/></svg>
        hello@meridianspine.com
      </li>
      <li>
        <svg viewBox="0 0 12 12" aria-hidden="true"><circle cx="6" cy="6" r="5" fill="none" stroke="#4a7fc4" stroke-width="1.1"/><ellipse cx="6" cy="6" rx="2.2" ry="5" fill="none" stroke="#4a7fc4" stroke-width="1"/><path d="M1 6 H11 M2 3.5 H10 M2 8.5 H10" stroke="#4a7fc4" stroke-width="0.9"/></svg>
        <span>www.<span class="accent">meridianspine</span>.com</span>
      </li>
    </ul>
    <address class="address">1187 Larkspur Lane<br>Corvallis, OR 97330</address>
  </section>

  <section class="card card--back" aria-label="Business card back">
    <div class="brand">
      <span class="brand__square" aria-hidden="true"></span>
      <span class="brand__name">MERIDIAN SPINE</span>
    </div>
  </section>
</body>
</html>
```